Call Center In Need of Website Design

We are a call center that provides inbound and outbound calling & marketing services for eCommerce store. We would like to see a fun, creative, playful design that is simple.

Here are some sample design sites we like;
- https://www.velmoreline.com/
- https://pindrask.io/
- https://www.glimbertic.com/live-chat-software/
- https://www.zavrolin.com/

Here are some competitor sites;
- https://www.ostrevaglinks.com/
- https://www.helpkestrel.com/

I have attached website content for your use.

Target Market(s)

eCommerce

Coding

Coded - Design and coding required

Number of Pages Required

5+ page

Font styles to use
Sans Serif

Colors

Designer to choose colors to be used in the design.

Requirements
Must have
• Must have designs for the following 5 separate pages;
• 1. Home (landing)
• - This will be were the design style really needs to show.
• - Just needs to touch on key services
• - CTA
• 2. About Us
• - Basic page for about me paragraph
• 3. Services
• - List of services with icons
• - Click on service type to expand details or hover over service icon to view popup bubble with details about that service
• 4. Pricing
• - Option to bundle 1(one) digital service plan and 1(one) call center service plan
• - Bundling adds 10% monthly discount to over all price
• - Customer does NOT have to bundle
• - FAQ
• 5. Contact Us
• - Include a capture form (name, company name, email, phone, message)
• - Contact info
• - Business hours
• When customer purchases their desired plan, then they are taken to a page where they must schedule a call with an account rep.
Nice to have
• home page animations
Should not have
• All information on Home/Landing page.

```html
<!DOCTYPE html>
<html lang="en">
<head>
<meta charset="utf-8">
<title>Corvella — Customer Service</title>
<link rel="stylesheet" href="https://fonts.googleapis.com/css2?family=Raleway:wght@400;500;600;700&family=Open+Sans:wght@400;600&display=swap">
<style>
:root{
  --dark:#1f1f1f;
  --darker:#171717;
  --teal:#55bb9c;
  --teal-deep:#4aa98c;
  --ink:#3a3f3f;
  --text:#555a5a;
  --muted:#8a8f8f;
  --panel:#b3b5b5;
  --white:#ffffff;
}
*{margin:0;padding:0;box-sizing:border-box}
html,body{width:1200px;height:2875px;overflow:hidden;background:var(--white)}
body{position:relative;font-family:"Raleway",sans-serif;color:var(--text)}
.abs{position:absolute}

/* header */
.site-header{left:0;top:0;width:1200px;height:98px;background:var(--dark)}
.brand{left:98px;top:26px;display:flex;align-items:center;gap:16px}
.brand-mark{width:44px;height:44px;border:3px solid var(--white);border-radius:50%}
.brand-name{font-family:"Raleway",sans-serif;font-weight:500;font-size:34px;letter-spacing:5px;color:var(--white)}
.main-nav{right:98px;top:36px;display:flex;gap:36px;font-size:12px;font-weight:600;color:var(--white)}
.main-nav .active{position:relative}
.main-nav .active::after{content:"";position:absolute;left:2px;right:2px;top:20px;height:2px;background:var(--teal)}

/* hero */
.hero{left:0;top:98px;width:1200px;height:557px;background:linear-gradient(100deg,#5b4f45 0%,#8c7d70 25%,#b4b3ae 55%,#7d8a88 80%,#9aa19c 100%)}
.hero-title{right:98px;top:286px;text-align:right;color:var(--white);font-size:40px;line-height:52px;font-weight:400}
.hero-title strong{font-weight:700;display:block}
.btn{display:inline-block;font-family:"Raleway",sans-serif;font-weight:700;font-size:15px;color:var(--white);text-align:center}
.btn-call{left:797px;top:406px;width:132px;height:48px;line-height:48px;background:var(--teal)}
.btn-learn{left:945px;top:406px;width:155px;height:48px;line-height:48px;background:#3a3d3d}
.hero-dot{left:290px;top:635px;width:12px;height:12px;border-radius:50%;background:rgba(255,255,255,.6)}

/* about */
.about-media{left:111px;top:740px;width:477px;height:312px;background:linear-gradient(120deg,#8a7f78,#d7d9db 55%,#bfc6cc);box-shadow:0 10px 22px rgba(0,0,0,.35)}
.play{left:320px;top:865px;width:60px;height:60px;border-radius:50%;background:rgba(80,70,65,.75)}
.play::after{content:"";position:absolute;left:24px;top:18px;border-left:18px solid var(--white);border-top:12px solid transparent;border-bottom:12px solid transparent}
.eyebrow{left:640px;top:748px;font-size:12px;font-weight:700;color:var(--teal);letter-spacing:.5px}
.about-title{left:640px;top:780px;font-size:27px;font-weight:700;color:var(--teal)}
.about-copy{left:640px;top:838px;width:440px;font-size:15px;line-height:26px;color:#4a4f4f}
.btn-read{left:640px;top:992px;width:142px;height:48px;line-height:48px;border-radius:24px;background:#3a4140;box-shadow:0 4px 10px rgba(0,0,0,.3)}

/* what we do */
.work-photo-left{left:0;top:1123px;width:356px;height:397px;background:linear-gradient(180deg,#d9c9b7,#f1f1f1 50%,#cfcfcf)}
.work-panel{left:356px;top:1123px;width:574px;height:397px;background:var(--panel)}
.work-photo-right{left:930px;top:1123px;width:270px;height:397px;background:linear-gradient(180deg,#c7b9a8,#f3f3f3 50%,#d5d5d5)}
.work-title{left:390px;top:1208px;font-size:20px;font-weight:600;color:var(--white)}
.work-rule{left:390px;top:1240px;width:50px;height:3px;background:var(--teal)}
.work-copy{left:390px;top:1258px;width:520px;font-family:"Open Sans",sans-serif;font-weight:600;font-size:15px;line-height:29px;color:var(--white)}
.btn-work{left:390px;top:1420px;width:142px;height:48px;line-height:48px;border-radius:24px;background:var(--teal)}

/* services */
.services-title{left:0;top:1574px;width:1200px;text-align:center;font-size:21px;font-weight:700;color:var(--teal)}
.services-rule{left:578px;top:1606px;width:44px;height:3px;background:var(--ink)}
.service{width:240px}
.service-head{display:flex;align-items:center;gap:10px;font-size:14px;font-weight:700;color:var(--ink);line-height:19px}
.service-icon{flex:none;width:36px;height:36px;border-radius:50%;background:#3a4140;display:flex;align-items:center;justify-content:center}
.service.on .service-head{color:var(--teal)}
.service.on .service-icon{background:var(--teal)}
.service p{margin-top:10px;font-family:"Open Sans",sans-serif;font-size:12px;line-height:18px;color:var(--muted)}
.dots{left:582px;top:1930px;display:flex;gap:4px}
.dots i{display:block;width:10px;height:10px;border-radius:50%;background:var(--teal)}
.dots i.off{background:transparent;border:2px solid var(--teal)}

/* digital */
.digital{left:0;top:2051px;width:1200px;height:467px;background:var(--teal)}
.digital-photo{left:0;top:2051px}
.digital-title{left:88px;top:2098px;font-size:21px;font-weight:700;color:var(--white)}
.digital-rule{left:88px;top:2128px;width:42px;height:3px;background:var(--white)}
.digital-list{left:88px;top:2153px;list-style:none}
.digital-list li{display:flex;align-items:center;gap:16px;height:54px;font-size:16px;font-weight:600;color:var(--white)}
.digital-list li span{width:28px;height:28px;border-radius:50%;background:var(--white);display:flex;align-items:center;justify-content:center}
.digital-list li span::after{content:"";width:12px;height:8px;border-radius:2px;background:var(--teal)}

/* footer */
.site-footer{left:0;top:2518px;width:1200px;height:297px;background:var(--dark)}
.foot-brand{left:100px;top:2574px;display:flex;align-items:center;gap:14px}
.foot-brand .brand-mark{width:40px;height:40px}
.foot-brand .brand-name{font-size:30px}
.foot-about{left:100px;top:2654px;width:280px;font-family:"Open Sans",sans-serif;font-size:12px;line-height:25px;color:#a8a8a8}
.socials{left:100px;top:2749px;display:flex;gap:14px}
.socials i{display:block;width:36px;height:36px;border-radius:50%;background:#2d2d2d}
.foot-head{font-size:22px;font-weight:500;color:var(--white)}
.contact-list{left:408px;top:2620px;list-style:none;font-family:"Open Sans",sans-serif;font-size:12px;color:#a8a8a8}
.contact-list li{display:flex;gap:16px;line-height:25px}
.contact-list li b{width:10px;height:10px;margin-top:8px;border-radius:2px;background:#8a8a8a;flex:none}
.contact-list li.pin b{border-radius:50% 50% 50% 0}
.quick-links{left:654px;top:2620px;list-style:none;font-family:"Open Sans",sans-serif;font-size:12px;color:#a8a8a8}
.quick-links li{line-height:24.5px;padding-left:24px;position:relative}
.quick-links li::before{content:"";position:absolute;left:2px;top:9px;border-left:5px solid #bbb;border-top:4px solid transparent;border-bottom:4px solid transparent}
.world-map{left:846px;top:2624px;width:230px;height:126px;border-radius:8px;background:radial-gradient(ellipse at center,#4a4a4a,#2c2c2c 75%)}
.copyright{left:0;top:2815px;width:1200px;height:60px;background:var(--darker);text-align:center;line-height:60px;font-family:"Open Sans",sans-serif;font-size:12px;color:#8f8f8f}
</style>
</head>
<body>

<header class="abs site-header">
  <div class="abs brand"><span class="brand-mark"></span><span class="brand-name">CORVELLA</span></div>
  <nav class="abs main-nav"><span class="active">HOME</span><span>ABOUT</span><span>SERVICE</span><span>PRICING</span><span>CONTACT</span></nav>
</header>

<section>
  <div class="abs hero" role="img" aria-label="Photo of a smiling support agent wearing a headset in a busy call center"></div>
  <h1 class="abs hero-title">WE OFFER INSTANT AND QUALITY<strong>CUSTOMER SERVICE!</strong></h1>
  <a class="abs btn btn-call">CALL NOW</a>
  <a class="abs btn btn-learn">LEARN MORE</a>
  <span class="abs hero-dot"></span>
</section>

<section>
  <div class="abs about-media" role="img" aria-label="Video still of agents with headsets working in a row"></div>
  <span class="abs play"></span>
  <p class="abs eyebrow">ABOUT US</p>
  <h2 class="abs about-title">Welcome to Corvella</h2>
  <p class="abs about-copy">Corvella is an omnichannel provider for customer care and back-end office support. We primarily work with eCommerce companies around the world. Our service is vital to the core operations and functionality of consumer-focused online eCommerce companies.</p>
  <a class="abs btn btn-read">READ MORE</a>
</section>

<section>
  <div class="abs work-photo-left" role="img" aria-label="Overhead photo of an agent typing at a desk"></div>
  <div class="abs work-panel"></div>
  <div class="abs work-photo-right" role="img" aria-label="Overhead photo of an agent working at a computer"></div>
  <h2 class="abs work-title">WHAT WE DO</h2>
  <span class="abs work-rule"></span>
  <p class="abs work-copy">Corvella is your personal customer service and product research team. We love eCommerce, but we love seeing business owners succeed even more! That is exactly why we have developed the processes and technology to take care of the most over looked areas in eCommerce -Customer Service andRetention.</p>
  <a class="abs btn btn-work">READ MORE</a>
</section>

<section>
  <h2 class="abs services-title">CALL CENTER SERVICES</h2>
  <span class="abs services-rule"></span>

  <div class="abs service on" style="left:98px;top:1670px">
    <div class="service-head"><span class="service-icon"><svg width="16" height="16" viewBox="0 0 24 24"><path fill="#fff" d="M6.6 10.8a15 15 0 006.6 6.6l2.2-2.2c.3-.3.7-.4 1-.2 1.1.4 2.3.6 3.6.6.6 0 1 .4 1 1V20c0 .6-.4 1-1 1A17 17 0 013 4c0-.6.4-1 1-1h3.5c.6 0 1 .4 1 1 0 1.3.2 2.5.6 3.6.1.3 0 .7-.2 1z"/></svg></span>ANSWERING SERVICE</div>
    <p>Lorem ipsum dolor sit amet, consectetur adipisicing elit</p>
  </div>
  <div class="abs service" style="left:355px;top:1670px">
    <div class="service-head"><span class="service-icon"><svg width="16" height="16" viewBox="0 0 24 24"><path fill="#fff" d="M6.6 10.8a15 15 0 006.6 6.6l2.2-2.2c.3-.3.7-.4 1-.2 1.1.4 2.3.6 3.6.6.6 0 1 .4 1 1V20c0 .6-.4 1-1 1A17 17 0 013 4c0-.6.4-1 1-1h3.5c.6 0 1 .4 1 1 0 1.3.2 2.5.6 3.6.1.3 0 .7-.2 1z"/></svg></span>WELCOME CALLS</div>
    <p>Lorem ipsum dolor sit amet, consectetur adipisicing elit</p>
  </div>
  <div class="abs service" style="left:612px;top:1670px">
    <div class="service-head"><span class="service-icon"><svg width="16" height="16" viewBox="0 0 24 24"><path fill="none" stroke="#fff" stroke-width="2.4" d="M4 12a8 8 0 1 0 3-6.2M4 4v4h4"/></svg></span>FOLLOW-UP SERVICE</div>
    <p>Lorem ipsum dolor sit amet, consectetur adipisicing elit</p>
  </div>
  <div class="abs service" style="left:869px;top:1670px">
    <div class="service-head"><span class="service-icon"><svg width="16" height="16" viewBox="0 0 24 24"><text x="12" y="18" text-anchor="middle" font-family="Open Sans, sans-serif" font-weight="700" font-size="17" fill="#fff">$</text></svg></span>CUSTOMER UPSELLING</div>
    <p>Lorem ipsum dolor sit amet, consectetur adipisicing elit</p>
  </div>
  <div class="abs service" style="left:98px;top:1788px">
    <div class="service-head"><span class="service-icon"><svg width="16" height="16" viewBox="0 0 24 24"><path fill="none" stroke="#fff" stroke-width="2.2" d="M4 6h9M4 20h14V11M9 15l10-10"/></svg></span>OVER-THE-PHONE<br>ORDER TAKING</div>
    <p>Lorem ipsum dolor sit amet, consectetur adipisicing elit</p>
  </div>
  <div class="abs service" style="left:355px;top:1788px">
    <div class="service-head"><span class="service-icon"><svg width="16" height="16" viewBox="0 0 24 24"><path fill="#fff" d="M12 3l8 4v10l-8 4-8-4V7z"/></svg></span>ORDER RETURN<br>PROCESSING</div>
    <p>Lorem ipsum dolor sit amet, consectetur adipisicing elit</p>
  </div>
  <div class="abs service" style="left:612px;top:1788px">
    <div class="service-head"><span class="service-icon"><svg width="16" height="16" viewBox="0 0 24 24"><path fill="none" stroke="#fff" stroke-width="2.4" d="M4 15v-3a8 8 0 0116 0v3"/><rect x="3" y="14" width="4" height="6" rx="1" fill="#fff"/><rect x="17" y="14" width="4" height="6" rx="1" fill="#fff"/></svg></span>FEEDBACK<br>SURVEY CALLS</div>
    <p>Lorem ipsum dolor sit amet, consectetur adipisicing elit</p>
  </div>
  <div class="abs service" style="left:869px;top:1788px">
    <div class="service-head"><span class="service-icon"><svg width="16" height="16" viewBox="0 0 24 24"><rect x="3" y="6" width="18" height="13" rx="1.5" fill="#fff"/><path d="M3 7l9 6 9-6" fill="none" stroke="#3a4140" stroke-width="1.6"/></svg></span>MESSAGE DELIVERING<br>SERVICE</div>
    <p>Lorem ipsum dolor sit amet, consectetur adipisicing elit</p>
  </div>

  <div class="abs dots"><i></i><i></i><i class="off"></i></div>
</section>

<section>
  <div class="abs digital"></div>
  <svg class="abs digital-photo" width="1200" height="467" viewBox="0 0 1200 467" role="img" aria-label="Photo of agents typing on keyboards in a row of computer workstations">
    <defs><linearGradient id="deskTones" x1="0" y1="0" x2="1" y2="1"><stop offset="0" stop-color="#6f8a80"/><stop offset=".45" stop-color="#c9c2b8"/><stop offset="1" stop-color="#3f4446"/></linearGradient></defs>
    <polygon points="622,0 1200,0 1200,467 530,467" fill="url(#deskTones)"/>
  </svg>
  <h2 class="abs digital-title">DIGITAL SERVICES</h2>
  <span class="abs digital-rule"></span>
  <ul class="abs digital-list">
    <li><span></span>Email Support</li>
    <li><span></span>Live Chat Support</li>
    <li><span></span>Product Research</li>
    <li><span></span>Product Listing</li>
    <li><span></span>Price Monitoring</li>
    <li><span></span>Product Photo &amp; Video Editing</li>
  </ul>
</section>

<footer>
  <div class="abs site-footer"></div>
  <div class="abs brand foot-brand"><span class="brand-mark"></span><span class="brand-name">CORVELLA</span></div>
  <p class="abs foot-about">Sed ut perspiciatis unde omnis iste natus error sit voluptatem accusantium doloremque laudantium, totam rem aperiam, eaque ipsa quae ab illo</p>
  <div class="abs socials"><i></i><i></i><i></i><i></i></div>

  <h3 class="abs foot-head" style="left:408px;top:2567px">CONTACT US</h3>
  <ul class="abs contact-list">
    <li class="pin"><b></b><span>Corvella, Inc. 412 Larkmoor St.<br>Dunvale, CA 90417</span></li>
    <li><b></b><span>info@corvella.com</span></li>
    <li><b></b><span>(555) 014-2290</span></li>
  </ul>

  <h3 class="abs foot-head" style="left:654px;top:2567px">QUICK LINKS</h3>
  <ul class="abs quick-links">
    <li>HOME</li><li>SERVICES</li><li>ABOUT</li><li>PRICING</li><li>CONTACT</li>
  </ul>

  <h3 class="abs foot-head" style="left:843px;top:2567px">OUR LOCATION</h3>
  <div class="abs world-map" role="img" aria-label="Dark world map with teal markers for office locations"></div>

  <div class="abs copyright">Copyrights © 2018 .All Rights Reserved.</div>
</footer>

</body>
</html>
```